I need a business card design for a new business based in South West Australia.
I specialize in residential window cleaning & general handyman maintenance.

Dale Marsh - 412 SILVER HAWK DETAILING
- Window Cleaning
- House Maintenance

```html
<!DOCTYPE html>
<html lang="en">
<head>
<meta charset="utf-8">
<title>Silver Hawk Detailing – Business Card</title>
<link href="https://fonts.googleapis.com/css2?family=Oswald:wght@500;600&family=Open+Sans:wght@400;600&display=swap" rel="stylesheet">
<style>
  :root {
    --page-bg: #ece9e4;
    --orange-light: #ffc20e;
    --orange-mid: #f4a716;
    --orange-deep: #e8891c;
    --accent-red: #e8541c;
    --card-white: #ffffff;
    --tint-cream: #fdf3e1;
    --text-dark: #3a3a3a;
    --text-muted: #555555;
  }
  * { box-sizing: border-box; margin: 0; padding: 0; }
  html, body {
    width: 1200px; height: 900px; overflow: hidden;
    background: var(--page-bg);
  }
  .sheet {
    width: 1200px; height: 900px;
    display: flex; flex-direction: column;
    align-items: center; justify-content: center; gap: 56px;
  }
  .card {
    position: relative;
    width: 640px; height: 366px;
    overflow: hidden;
    box-shadow: 0 6px 18px rgba(0,0,0,.18);
  }

  /* Front */
  .card--front {
    background: radial-gradient(circle at 50% 38%, var(--orange-light) 0%, var(--orange-mid) 45%, var(--orange-deep) 100%);
  }
  .front-brand {
    position: absolute; left: 140px; top: 196px; width: 400px;
    transform: rotate(-5deg); transform-origin: left center;
  }
  .front-brand__name {
    font-family: 'Oswald', sans-serif; font-weight: 600;
    font-size: 40px; line-height: 1; color: var(--card-white);
    letter-spacing: .5px; white-space: nowrap;
  }
  .front-brand__tagline {
    margin-top: 6px;
    font-family: 'Open Sans', sans-serif; font-weight: 600;
    font-size: 13.5px; color: var(--card-white); letter-spacing: .6px;
    white-space: nowrap;
  }

  /* Back */
  .card--back {
    background: linear-gradient(180deg, var(--card-white) 0%, var(--card-white) 55%, var(--tint-cream) 100%);
  }
  .back-brand {
    position: absolute; left: 40px; top: 118px; width: 330px;
    transform: rotate(-4deg); transform-origin: left center;
  }
  .back-brand__mark {
    width: 30px; height: 30px; border-radius: 50%;
    background: var(--orange-mid); margin: 0 0 10px 120px;
  }
  .back-brand__name {
    font-family: 'Oswald', sans-serif; font-weight: 600;
    font-size: 34px; line-height: 1; color: var(--orange-mid);
    white-space: nowrap;
  }
  .back-brand__tagline {
    margin-top: 3px;
    font-family: 'Open Sans', sans-serif; font-weight: 600;
    font-size: 11.5px; color: var(--accent-red); letter-spacing: .5px;
    white-space: nowrap;
  }
  .contact {
    position: absolute; left: 420px; top: 122px;
    transform: rotate(-4deg); transform-origin: left top;
  }
  .contact__name {
    font-family: 'Open Sans', sans-serif; font-weight: 600;
    font-size: 19px; color: var(--orange-mid);
  }
  .contact__role {
    font-family: 'Open Sans', sans-serif; font-size: 12.5px;
    color: var(--text-dark); margin-bottom: 22px;
  }
  .contact__list { list-style: none; }
  .contact__item {
    display: flex; align-items: center; gap: 8px;
    font-family: 'Open Sans', sans-serif; font-size: 13.5px;
    color: var(--text-muted); line-height: 1.55;
  }
  .contact__icon { width: 12px; height: 12px; flex: none; }
  .contact__icon * { fill: var(--orange-mid); }
</style>
</head>
<body>
<main class="sheet">
  <section class="card card--front" aria-label="Card front">
    <div class="front-brand">
      <div class="front-brand__name">SILVER HAWK DETAILING</div>
      <div class="front-brand__tagline">WINDOW CLEANING &amp; HOUSE MAINTENANCE</div>
    </div>
  </section>

  <section class="card card--back" aria-label="Card back">
    <div class="back-brand">
      <div class="back-brand__mark"></div>
      <div class="back-brand__name">SILVER HAWK DETAILING</div>
      <div class="back-brand__tagline">WINDOW CLEANING &amp; HOUSE MAINTENANCE</div>
    </div>

    <div class="contact">
      <div class="contact__name">Dale Marsh</div>
      <div class="contact__role">Managing Director</div>
      <ul class="contact__list">
        <li class="contact__item">
          <svg class="contact__icon" viewBox="0 0 12 12"><path d="M2.5 1 4.5 3.2 3.6 4.6a7 7 0 0 0 3.8 3.8l1.4-.9L11 9.5 9.8 11C5 10.6 1.4 7 1 2.2z"/></svg>
          08-9412-3306
        </li>
        <li class="contact__item">
          <svg class="contact__icon" viewBox="0 0 12 12"><rect x="1" y="4" width="10" height="7" rx="1"/><rect x="3" y="1" width="6" height="3"/></svg>
          08-9412-3307
        </li>
        <li class="contact__item">
          <svg class="contact__icon" viewBox="0 0 12 12"><path d="M3 0h6a1 1 0 0 1 1 1v10a1 1 0 0 1-1 1H3a1 1 0 0 1-1-1V1a1 1 0 0 1 1-1zm0 2v7h6V2z"/></svg>
          0412-735-908
        </li>
        <li class="contact__item">
          <svg class="contact__icon" viewBox="0 0 12 12"><path d="M1 2h10v1L6 6.5 1 3z"/><path d="M1 4.2 6 7.7l5-3.5V10H1z"/></svg>
          hello@silverhawkwa.au
        </li>
        <li class="contact__item">
          <svg class="contact__icon" viewBox="0 0 12 12"><path d="M5 7 7 5M4.5 5.5 2.8 7.2a1.6 1.6 0 0 0 2 2L6.5 7.5M7.5 6.5 9.2 4.8a1.6 1.6 0 0 0-2-2L5.5 4.5" stroke="#f4a716" stroke-width="1.4" fill="none"/></svg>
          www.silverhawkwa.au
        </li>
      </ul>
    </div>
  </section>
</main>
</body>
</html>
```